Kestrelway Financial Plans

I am looking for a complete resdesign of my small financial presentation. This is a Word Doc/PDF that I print off when meeting with people in private. I often present my "two pager" that I have been using for years and years. It tells them the basics of what I do, how I help people and foundational financial principles.

I have recently gone out on my own in business and have completely rebranded. This presentation is my most used tool, so it is the first of many things I would like to redo. I am hoping it will somehow coordinate with the colors of my business, not necessarily the EXACT same 3 colors everywhere, but have the design colors compliment.

I've uploaded all my logo designs, as well as the current "two-pager". I am not against it going to 3 pages if needed. As it will still land on 2 pages with duplex printing.

It has always been VERY simple. I am wanting it built into a more professional and design specific format, to show off my branding, without being over cluttered.

I am completely open to ANY graphics changes. Obviously some are very novice, the house on the last page has always been overly simplified.

```html
<!DOCTYPE html>
<html lang="en">
<head>
<meta charset="utf-8">
<title>Kestrelway Financial Plans – Two Pager</title>
<link rel="stylesheet" href="https://fonts.googleapis.com/css2?family=Montserrat:wght@600;700;800&family=Roboto:wght@400;500;700&display=swap">
<style>
:root{
  --backdrop:#808080;
  --navy:#111827;
  --green:#17a336;
  --mint:#d5f0d5;
  --white:#ffffff;
  --ink:#1b1f27;
  --muted:#555b66;
  --slate:#6c727c;
  --blue:#2b5ca7;
  --indigo:#18194a;
  --rule:#d9dde2;
}
*{box-sizing:border-box;margin:0;padding:0}
html,body{width:1200px;height:1086px;overflow:hidden}
body{background:var(--backdrop);font-family:"Roboto",Arial,sans-serif;color:var(--ink);position:relative}
.page{position:absolute;top:46px;width:540px;height:994px;background:var(--white);overflow:hidden}
.page--left{left:44px}
.page--right{left:616px}
.abs{position:absolute}

.masthead{position:absolute;left:0;top:0;width:540px;height:81px;background:var(--navy);
  background-image:radial-gradient(ellipse 60px 14px at 70px 56px,rgba(23,163,54,.18),transparent),radial-gradient(ellipse 60px 14px at 470px 56px,rgba(23,163,54,.18),transparent)}
.brand{position:absolute;left:0;right:0;text-align:center;color:var(--white)}
.brand__name{font-family:"Montserrat",Arial,sans-serif;font-weight:700;font-size:27px;letter-spacing:1px;line-height:1}
.brand__sub{font-family:"Montserrat",Arial,sans-serif;font-weight:700;font-size:9.5px;letter-spacing:3px;margin-top:6px}
.masthead .brand{top:20px}

.ribbon{position:absolute;background:var(--green);color:var(--white);font-family:"Montserrat",Arial,sans-serif;font-weight:800;
  display:flex;align-items:center;justify-content:center;font-size:17.5px;letter-spacing:.3px;
  clip-path:polygon(0 0,100% 0,calc(100% - 24px) 100%,24px 100%)}

.mint-band{position:absolute;left:0;width:540px;background:var(--mint)}

/* challenge cards */
.card{position:absolute;top:147px;width:159px;height:173px;background:var(--white);box-shadow:0 2px 8px rgba(0,0,0,.13)}
.card__title{position:absolute;left:11px;top:15px;font-family:"Montserrat",Arial,sans-serif;font-weight:700;font-size:12.5px}
.card__icon{position:absolute;right:10px;top:9px;width:28px;height:28px;border-radius:50%;background:var(--green)}
.card__rule{position:absolute;left:11px;right:0;top:46px;height:1px;background:var(--rule)}
.card__list{position:absolute;left:11px;right:8px;top:62px;list-style:none}
.card__list li{position:relative;padding-left:10px;font-size:5.3px;line-height:8.7px;color:var(--muted);margin-bottom:8px}
.card__list li::before{content:"";position:absolute;left:0;top:2px;width:4.5px;height:4.5px;border-radius:50%;background:var(--green)}
.card__src{display:block;font-style:italic;margin-top:3px;color:var(--ink)}

/* process */
.step{position:absolute;top:431px;width:78px;height:70px;background:var(--navy);border-radius:4px;color:var(--white);
  font-weight:500;font-size:8.2px;line-height:10px;text-align:center;display:flex;flex-direction:column;align-items:center;justify-content:flex-start;padding-top:16px}
.step__icon{width:22px;height:18px;border-radius:3px;background:var(--green);opacity:.85;margin-bottom:6px}
.step-arrow{position:absolute;top:459px;width:15px;height:15px}
.pill{position:absolute;left:204px;top:524px;width:131px;height:28px;border-radius:14px;background:var(--slate);color:var(--white);
  font-weight:700;font-size:8px;display:flex;align-items:center;justify-content:center;letter-spacing:.2px}

/* how section */
.need{position:absolute;width:50px;height:50px;border-radius:50%;background:radial-gradient(circle at 40% 35%,#f4f5f6,#c9ccd0);
  border:4px solid var(--navy);border-left-color:#c9ccd0;border-bottom-color:#c9ccd0}
.need-label{position:absolute;width:110px;text-align:center;font-weight:700;font-size:8.3px}
.spine{position:absolute;left:199px;top:675px;width:54px;height:260px;border-radius:27px;background:var(--navy)}
.spine__dot{position:absolute;left:206px;width:40px;height:40px;border-radius:50%;background:radial-gradient(circle at 40% 35%,#f4f5f6,#bfc3c8)}
.spine__label{position:absolute;left:199px;width:54px;text-align:center;color:var(--white);font-weight:700;font-size:7.6px;line-height:10px;white-space:nowrap}
.center-cap{position:absolute;left:176px;width:100px;text-align:center;font-weight:700;font-size:8.3px}
.flow-label{position:absolute;font-size:7.5px;font-weight:500;color:var(--green)}
.partner{position:absolute;width:76px;height:34px;background:var(--white);box-shadow:0 1px 5px rgba(0,0,0,.14);
  display:flex;align-items:center;justify-content:center;gap:4px;font-weight:700;font-size:7.6px;color:var(--navy)}
.partner__dot{width:7px;height:7px;border-radius:50%;background:var(--green);flex:none}
.foot-bar{position:absolute;left:0;bottom:0;width:540px;height:12px;background:var(--green)}

/* charts */
.chart{position:absolute;background:var(--white);border:1px solid #e3e6ea;border-radius:6px}
.chart svg{display:block}
.badge{position:absolute;width:20px;height:20px;border-radius:50%;background:#eef0f2;box-shadow:0 1px 3px rgba(0,0,0,.2);
  font-weight:700;font-size:6.3px;display:flex;align-items:center;justify-content:center}
.chart text{font-family:"Roboto",Arial,sans-serif}

/* tax house */
.roof{position:absolute;left:16px;top:667px;width:508px;height:80px}
.tax-cell{position:absolute;height:29px;display:flex;align-items:center;justify-content:center;text-align:center;color:var(--white);
  font-size:7.4px;line-height:8.8px;padding:0 6px}
.tax-cell--head{font-weight:700;font-size:9.5px}
.tax-cell--foot{font-weight:700;font-size:8.6px}
.c-green{background:var(--green)}
.c-slate{background:var(--slate)}
.c-navy{background:var(--navy)}
.c-blue{background:var(--blue)}
.c-indigo{background:var(--indigo)}
</style>
</head>
<body>

<section class="page page--left">
  <header class="masthead">
    <div class="brand"><div class="brand__name">KESTRELWAY</div><div class="brand__sub">FINANCIAL PLANS</div></div>
  </header>

  <h2 class="ribbon" style="left:85px;top:81px;width:371px;height:39px">THE FINANCIAL CHALLENGE</h2>

  <article class="card" style="left:16px">
    <h3 class="card__title">Savings</h3>
    <div class="card__icon" role="img" aria-label="Hand holding a dollar coin icon"></div>
    <div class="card__rule"></div>
    <ul class="card__list">
      <li>49% Of Canadian Employees Are Living Paycheque To Paycheque. 25% Of Canadians Are Unable To Cover An Unexpected $500 Expense<span class="card__src">- National Data Office (Feb 2023)</span></li>
      <li>25% Of Canadians Need To Access Their Retirement Savings Early. 20% Of Canadians Have No Savings. 39% Of Canadians Aged 55-65 Have Less Than $5,000 In Savings.<span class="card__src">- National Data Office (Feb 2023)</span></li>
    </ul>
  </article>

  <article class="card" style="left:190px">
    <h3 class="card__title">Debt</h3>
    <div class="card__icon" role="img" aria-label="Money bag labelled debt icon"></div>
    <div class="card__rule"></div>
    <ul class="card__list">
      <li>The Average Canadian Has $22,131 In Consumer Debt. Which Excludes Mortgages.<span class="card__src">- Creditline Research (Aug 2024)</span></li>
      <li>Over 55% Of Canadians Hold Credit Card Debt And The Total Canadian Household Debt Has Increased To $2.52trillion, Including Consumer Credit, Mortgage And Non-mortgage Loans.<span class="card__src">- Lenders Council (Aug 2024)</span></li>
    </ul>
  </article>

  <article class="card" style="left:364px">
    <h3 class="card__title">Insurance</h3>
    <div class="card__icon" role="img" aria-label="Medical document with shield icon"></div>
    <div class="card__rule"></div>
    <ul class="card__list">
      <li>45% Of Canadians Do Not Have Individual Life Insurance Coverage, But 48% Say Their Families Would Face Financial Trouble Within 6 Months Of Losing Someone<span class="card__src">- Lifeview Intl. (Apr 2023)</span></li>
      <li>2-in-5 Canadians (43% Women / 44% Men) Will Be Diagosed With A Form Of Cancer Or Other Critical Illness During Their Lifetime. Every 7 Seconds.<span class="card__src">- Health Data Portal (June 2024)</span></li>
    </ul>
  </article>

  <div class="mint-band" style="top:364px;height:227px"></div>
  <h2 class="ribbon" style="left:67px;top:364px;width:407px;height:38px">WHO ARE WE AND WHAT DO WE DO?</h2>

  <div class="step" style="left:16px"><span class="step__icon" role="img" aria-label="Cash stack icon"></span>Cash Flow</div>
  <div class="step" style="left:102px"><span class="step__icon" role="img" aria-label="Hands holding shield icon"></span>Cash Flow<br>Protection</div>
  <div class="step" style="left:188px"><span class="step__icon" role="img" aria-label="Debt chart icon"></span>Debt<br>Management</div>
  <div class="step" style="left:274px"><span class="step__icon" role="img" aria-label="Umbrella over money bag icon"></span>Emergency Fund</div>
  <div class="step" style="left:360px"><span class="step__icon" role="img" aria-label="Growing money plant icon"></span>Build Wealth</div>
  <div class="step" style="left:446px"><span class="step__icon" role="img" aria-label="Family home icon"></span>Preserve</div>

  <svg class="step-arrow" style="left:91px" viewBox="0 0 15 15"><circle cx="7.5" cy="7.5" r="7.5" fill="#17a336"/><path d="M4 7.5h7M8.3 4.8l2.7 2.7-2.7 2.7" stroke="#fff" stroke-width="1.2" fill="none"/></svg>
  <svg class="step-arrow" style="left:177px" viewBox="0 0 15 15"><circle cx="7.5" cy="7.5" r="7.5" fill="#17a336"/><path d="M4 7.5h7M8.3 4.8l2.7 2.7-2.7 2.7" stroke="#fff" stroke-width="1.2" fill="none"/></svg>
  <svg class="step-arrow" style="left:263px" viewBox="0 0 15 15"><circle cx="7.5" cy="7.5" r="7.5" fill="#17a336"/><path d="M4 7.5h7M8.3 4.8l2.7 2.7-2.7 2.7" stroke="#fff" stroke-width="1.2" fill="none"/></svg>
  <svg class="step-arrow" style="left:349px" viewBox="0 0 15 15"><circle cx="7.5" cy="7.5" r="7.5" fill="#17a336"/><path d="M4 7.5h7M8.3 4.8l2.7 2.7-2.7 2.7" stroke="#fff" stroke-width="1.2" fill="none"/></svg>
  <svg class="step-arrow" style="left:435px" viewBox="0 0 15 15"><circle cx="7.5" cy="7.5" r="7.5" fill="#17a336"/><path d="M4 7.5h7M8.3 4.8l2.7 2.7-2.7 2.7" stroke="#fff" stroke-width="1.2" fill="none"/></svg>

  <div class="pill">EDUCATION &amp; AWARENESS</div>

  <h2 class="ribbon" style="left:112px;top:591px;width:316px;height:38px">HOW ARE WE DOING IT?</h2>

  <svg class="abs" style="left:0;top:640px" width="540" height="300" viewBox="0 640 540 300">
    <g stroke="#9aa0a8" stroke-width="0.8" fill="none">
      <path d="M78 690H117V906H78M117 798H199"/>
      <path d="M253 798H335M335 714V898M335 714H361M335 760H361M335 806H361M335 852H361M335 898H361"/>
    </g>
  </svg>

  <div class="need" style="left:27px;top:665px" role="img" aria-label="Home and money icon"></div>
  <div class="need-label" style="left:-3px;top:721px">Living Expenses</div>
  <div class="need" style="left:27px;top:773px" role="img" aria-label="Tax document icon"></div>
  <div class="need-label" style="left:-3px;top:828px">Taxes</div>
  <div class="need" style="left:27px;top:881px" role="img" aria-label="Hand holding percentage card icon"></div>
  <div class="need-label" style="left:-3px;top:937px">Debt</div>

  <div class="flow-label" style="left:145px;top:782px">Savings</div>
  <div class="flow-label" style="left:282px;top:782px">Pay Us</div>

  <div class="center-cap" style="top:660px">Retirement Savings</div>
  <div class="spine"></div>
  <div class="spine__dot" style="top:681px" role="img" aria-label="Retiree in rocking chair icon"></div>
  <div class="spine__label" style="top:733px">Children's<br>Education</div>
  <div class="spine__dot" style="top:758px" role="img" aria-label="Graduate student icon"></div>
  <div class="spine__label" style="top:809px">Proper<br>Protection</div>
  <div class="spine__dot" style="top:834px" role="img" aria-label="Protective shield icon"></div>
  <div class="spine__dot" style="top:886px" role="img" aria-label="Falling debt chart icon"></div>
  <div class="center-cap" style="top:943px">Freedom From Debt</div>

  <div class="partner" style="left:361px;top:697px"><span class="partner__dot"></span>Maplecrest Life</div>
  <div class="partner" style="left:448px;top:697px">Northfield Life</div>
  <div class="partner" style="left:361px;top:743px">Daybreak Financial</div>
  <div class="partner" style="left:448px;top:743px">Harbourline</div>
  <div class="partner" style="left:361px;top:789px">Arcadia Group</div>
  <div class="partner" style="left:448px;top:789px">Ridgeway Insurance</div>
  <div class="partner" style="left:361px;top:835px">Veltara</div>
  <div class="partner" style="left:448px;top:835px">Lakeshore Insurance</div>
  <div class="partner" style="left:361px;top:881px">Commonfold</div>
  <div class="partner" style="left:448px;top:881px">Orvana</div>

  <div class="foot-bar"></div>
</section>

<section class="page page--right">
  <header class="masthead">
    <div class="brand"><div class="brand__name">KESTRELWAY</div><div class="brand__sub">FINANCIAL PLANS</div></div>
  </header>

  <h2 class="ribbon" style="left:161px;top:81px;width:217px;height:39px">RULE OF 72</h2>

  <div class="chart" style="left:27px;top:151px;width:148px;height:166px">
    <svg width="148" height="166" viewBox="0 0 148 166">
      <text x="23" y="12" font-size="5.6" font-weight="700">Money Doubles Every 18 Year</text>
      <g font-size="4.5" fill="#1b1f27">
        <text x="8" y="86">Age 65</text><text x="8" y="111">Age 47</text><text x="8" y="137">Age 29</text>
      </g>
      <line x1="28" y1="74" x2="28" y2="142" stroke="#ccc" stroke-width=".5"/>
      <rect x="28" y="78" width="80" height="5" fill="#111827"/><rect x="28" y="83" width="90" height="5" fill="#17a336"/>
      <rect x="28" y="103" width="66" height="5" fill="#111827"/><rect x="28" y="108" width="52" height="5" fill="#17a336"/>
      <rect x="28" y="129" width="52" height="5" fill="#111827"/><rect x="28" y="134" width="29" height="5" fill="#17a336"/>
      <g font-size="4.3" fill="#1b1f27"><text x="111" y="82">65</text><text x="97" y="107">53</text><text x="83" y="133">41</text></g>
      <g font-size="4.3" fill="#17a336"><text x="121" y="88">$80,000</text><text x="83" y="113">$40,000</text><text x="60" y="139">$20,000</text></g>
      <rect x="52" y="150" width="3" height="3" fill="#111827"/><text x="57" y="153" font-size="4.3">Age</text>
      <rect x="75" y="150" width="3" height="3" fill="#17a336"/><text x="80" y="153" font-size="4.3">Amount</text>
    </svg>
  </div>
  <div class="badge" style="left:22px;top:143px">4%</div>

  <div class="chart" style="left:197px;top:151px;width:148px;height:166px">
    <svg width="148" height="166" viewBox="0 0 148 166">
      <text x="23" y="12" font-size="5.6" font-weight="700">Money Doubles Every 12 Years</text>
      <g font-size="4.5" fill="#1b1f27">
        <text x="8" y="60">Age 65</text><text x="8" y="86">Age 53</text><text x="8" y="111">Age 41</text><text x="8" y="137">Age 29</text>
      </g>
      <line x1="28" y1="48" x2="28" y2="142" stroke="#ccc" stroke-width=".5"/>
      <rect x="28" y="52" width="80" height="5" fill="#111827"/><rect x="28" y="57" width="90" height="5" fill="#17a336"/>
      <rect x="28" y="78" width="64" height="5" fill="#111827"/><rect x="28" y="83" width="54" height="5" fill="#17a336"/>
      <rect x="28" y="103" width="51" height="5" fill="#111827"/><rect x="28" y="108" width="32" height="5" fill="#17a336"/>
      <rect x="28" y="129" width="37" height="5" fill="#111827"/><rect x="28" y="134" width="18" height="5" fill="#17a336"/>
      <g font-size="4.3" fill="#1b1f27"><text x="111" y="56">65</text><text x="95" y="82">53</text><text x="82" y="107">41</text><text x="68" y="133">29</text></g>
      <g font-size="4.3" fill="#17a336"><text x="121" y="62">$80,000</text><text x="85" y="88">$40,000</text><text x="63" y="113">$20,000</text><text x="49" y="139">$10,000</text></g>
      <rect x="52" y="150" width="3" height="3" fill="#111827"/><text x="57" y="153" font-size="4.3">Age</text>
      <rect x="75" y="150" width="3" height="3" fill="#17a336"/><text x="80" y="153" font-size="4.3">Amount</text>
    </svg>
  </div>
  <div class="badge" style="left:192px;top:143px">6%</div>

  <div class="chart" style="left:368px;top:151px;width:148px;height:166px">
    <svg width="148" height="166" viewBox="0 0 148 166">
      <text x="23" y="12" font-size="5.6" font-weight="700">Money Doubles Every 9 Years</text>
      <g font-size="4.5" fill="#1b1f27">
        <text x="8" y="35">Age 65</text><text x="8" y="60">Age 56</text><text x="8" y="86">Age 47</text><text x="8" y="111">Age 38</text><text x="8" y="137">Age 29</text>
      </g>
      <line x1="28" y1="23" x2="28" y2="142" stroke="#ccc" stroke-width=".5"/>
      <rect x="28" y="27" width="80" height="5" fill="#111827"/><rect x="28" y="32" width="90" height="5" fill="#17a336"/>
      <rect x="28" y="52" width="74" height="5" fill="#111827"/><rect x="28" y="57" width="68" height="5" fill="#17a336"/>
      <rect x="28" y="78" width="64" height="5" fill="#111827"/><rect x="28" y="83" width="46" height="5" fill="#17a336"/>
      <rect x="28" y="103" width="51" height="5" fill="#111827"/><rect x="28" y="108" width="29" height="5" fill="#17a336"/>
      <rect x="28" y="129" width="37" height="5" fill="#111827"/><rect x="28" y="134" width="14" height="5" fill="#17a336"/>
      <g font-size="4.3" fill="#1b1f27"><text x="111" y="31">65</text><text x="105" y="56">56</text><text x="95" y="82">47</text><text x="82" y="107">38</text><text x="68" y="133">29</text></g>
      <g font-size="4.3" fill="#17a336"><text x="121" y="37">$160,000</text><text x="99" y="62">$80,000</text><text x="77" y="88">$40,000</text><text x="60" y="113">$20,000</text><text x="45" y="139">$10,000</text></g>
      <rect x="52" y="150" width="3" height="3" fill="#111827"/><text x="57" y="153" font-size="4.3">Age</text>
      <rect x="75" y="150" width="3" height="3" fill="#17a336"/><text x="80" y="153" font-size="4.3">Amount</text>
    </svg>
  </div>
  <div class="badge" style="left:363px;top:143px">8%</div>

  <div class="chart" style="left:137px;top:347px;width:269px;height:221px">
    <svg width="269" height="221" viewBox="0 0 269 221">
      <text x="23" y="13" font-size="6" font-weight="700">Money Doubles Every 6 Years</text>
      <g font-size="4.8" fill="#1b1f27">
        <text x="8" y="38">Age 65</text><text x="8" y="63">Age 59</text><text x="8" y="88">Age 53</text><text x="8" y="114">Age 47</text><text x="8" y="139">Age 41</text><text x="8" y="164">Age 35</text><text x="8" y="190">Age 29</text>
      </g>
      <line x1="29" y1="26" x2="29" y2="196" stroke="#ccc" stroke-width=".5"/>
      <rect x="29" y="29" width="180" height="5.5" fill="#111827"/><rect x="29" y="34.5" width="203" height="5.5" fill="#17a336"/>
      <rect x="29" y="54" width="164" height="5.5" fill="#111827"/><rect x="29" y="59.5" width="133" height="5.5" fill="#17a336"/>
      <rect x="29" y="79" width="141" height="5.5" fill="#111827"/><rect x="29" y="84.5" width="113" height="5.5" fill="#17a336"/>
      <rect x="29" y="105" width="164" height="5.5" fill="#111827"/><rect x="29" y="110.5" width="152" height="5.5" fill="#17a336"/>
      <rect x="29" y="130" width="144" height="5.5" fill="#111827"/><rect x="29" y="135.5" width="104" height="5.5" fill="#17a336"/>
      <rect x="29" y="155" width="115" height="5.5" fill="#111827"/><rect x="29" y="160.5" width="64" height="5.5" fill="#17a336"/>
      <rect x="29" y="181" width="83" height="5.5" fill="#111827"/><rect x="29" y="186.5" width="32" height="5.5" fill="#17a336"/>
      <g font-size="4.6" fill="#1b1f27"><text x="212" y="33">65</text><text x="196" y="58">59</text><text x="173" y="83">53</text><text x="196" y="109">47</text><text x="176" y="134">41</text><text x="147" y="159">35</text><text x="115" y="185">29</text></g>
      <g font-size="4.6" fill="#17a336"><text x="235" y="40">$640,000</text><text x="165" y="65">$320,000</text><text x="145" y="90">$160,000</text><text x="184" y="116">$80,000</text><text x="136" y="141">$40,000</text><text x="96" y="166">$20,000</text><text x="64" y="192">$10,000</text></g>
      <rect x="113" y="207" width="3.2" height="3.2" fill="#111827"/><text x="118" y="210.5" font-size="4.6">Age</text>
      <rect x="136" y="207" width="3.2" height="3.2" fill="#17a336"/><text x="141" y="210.5" font-size="4.6">Amount</text>
    </svg>
  </div>
  <div class="badge" style="left:132px;top:339px">12%</div>

  <div class="mint-band" style="top:605px;height:389px"></div>
  <h2 class="ribbon" style="left:161px;top:605px;width:217px;height:38px">TAXES</h2>

  <svg class="roof" viewBox="0 0 508 80" preserveAspectRatio="none"><polygon points="254,0 508,80 0,80" fill="#111827"/></svg>
  <div class="brand" style="top:701px">
    <div class="brand__name" style="font-size:19px">KESTRELWAY</div>
    <div class="brand__sub" style="font-size:7px;margin-top:4px;letter-spacing:2.4px">FINANCIAL PLANS</div>
  </div>

  <div class="tax-cell tax-cell--head c-green" style="left:16px;top:753px;width:124px">HOME</div>
  <div class="tax-cell tax-cell--head c-green" style="left:144px;top:753px;width:124px">RRSP</div>
  <div class="tax-cell tax-cell--head c-green" style="left:272px;top:753px;width:124px">TFSA</div>
  <div class="tax-cell tax-cell--head c-green" style="left:400px;top:753px;width:124px">PERM LIFE</div>

  <div class="tax-cell c-slate" style="left:16px;top:788px;width:124px">Partner With Mortgage Brokers For Best Rates</div>
  <div class="tax-cell c-navy" style="left:144px;top:788px;width:124px">Tax Deduction</div>
  <div class="tax-cell c-blue" style="left:272px;top:788px;width:124px">No Tax Deductions</div>
  <div class="tax-cell c-indigo" style="left:400px;top:788px;width:124px">No Tax Deduction</div>

  <div class="tax-cell c-slate" style="left:16px;top:822px;width:124px">Mortgage Insurance Alternatives</div>
  <div class="tax-cell c-navy" style="left:144px;top:822px;width:124px">Tax Deferred</div>
  <div class="tax-cell c-blue" style="left:272px;top:822px;width:124px">Tax Free Growth</div>
  <div class="tax-cell c-indigo" style="left:400px;top:822px;width:124px">Qualify</div>

  <div class="tax-cell c-blue" style="left:16px;top:857px;width:252px">2009 - $95,000</div>
  <div class="tax-cell c-indigo" style="left:272px;top:857px;width:252px">Tax Deferred Growth</div>

  <div class="tax-cell c-blue" style="left:16px;top:891px;width:508px">Limit 2023 - $7,000/YR</div>

  <div class="tax-cell tax-cell--foot c-green" style="left:16px;top:926px;width:124px">Sell</div>
  <div class="tax-cell tax-cell--foot c-green" style="left:144px;top:926px;width:124px">100% Tax</div>
  <div class="tax-cell tax-cell--foot c-green" style="left:272px;top:926px;width:124px">0% Tax</div>
  <div class="tax-cell tax-cell--foot c-green" style="left:400px;top:926px;width:124px">0% Tax</div>

  <div class="foot-bar"></div>
</section>

</body>
</html>
```